Upland Bird Hunting Preserve and Pointing Dog kennel

Need Price packages outlined for the bird hunting business. List the kennel and that we provide training and dogs for sale.
The preserve is "Tall Heron Provisions" the dog kennel is "Pine Hollow Setters"
1/2 Day Upland Field Hunts: 5 Pheasants $120
7 Chukar $125
Continental Hunt 12 Pheasants $325 includes meal, minimum 12 hunters
Guides available $100

Target Market(s)

upland bird hunters

Industry/Entity Type

hunting, outdoor

Colors
EE7325
F08F49
F5BC92
FAE3D3
FDF4ED

```html
<!DOCTYPE html>
<html lang="en">
<head>
<meta charset="utf-8">
<title>Tall Heron Provisions — Hunting Packages</title>
<link rel="stylesheet" href="https://fonts.googleapis.com/css2?family=Libre+Baskerville:ital,wght@0,400;0,700;1,400;1,700&display=swap">
<style>
  :root {
    --orange: #EE7325;
    --orange-soft: #F08F49;
    --peach: #F5BC92;
    --blush: #FAE3D3;
    --paper: #FDEAE0;
    --ink: #1b1b1b;
    --ink-soft: #3a3a3a;
  }
  * { margin: 0; padding: 0; box-sizing: border-box; }
  html, body { width: 927px; height: 1200px; overflow: hidden; background: var(--paper); }
  body { font-family: "Libre Baskerville", Georgia, serif; color: var(--ink); }
  .flyer { position: relative; width: 927px; height: 1200px; background: var(--paper); }
  .frame { position: absolute; left: 55px; top: 55px; width: 818px; height: 1089px; border: 3px solid var(--orange-soft); }
  .abs { position: absolute; white-space: nowrap; }
  .center { left: 0; right: 0; text-align: center; }
  .title { top: 36px; display: flex; justify-content: center; }
  .title span { background: var(--paper); padding: 0 18px; font-weight: 700; font-size: 30px; line-height: 38px; letter-spacing: 0.5px; }
  .town { top: 74px; font-weight: 700; font-size: 22px; line-height: 26px; }
  .tagline { top: 108px; font-weight: 700; font-size: 21px; line-height: 26px; color: var(--orange); letter-spacing: 2px; }

  .photo { position: absolute; background: #fff; }
  .photo .fill { width: 100%; height: 100%; }
  .photo-hero { left: 89px; top: 136px; width: 752px; height: 279px; padding: 5px; }
  .photo-hero .fill {
    background:
      radial-gradient(ellipse 60% 22% at 55% 52%, rgba(196,96,52,0.55), transparent 70%),
      linear-gradient(180deg, #a89a86 0%, #b9ab95 22%, #7c6d60 45%, #6e5446 62%, #a08a74 78%, #c9bca8 100%);
  }
  .photo-small { top: 787px; width: 366px; height: 206px; padding: 5px; background: var(--orange); }
  .photo-left { left: 91px; }
  .photo-left .fill {
    background:
      radial-gradient(ellipse 30% 35% at 42% 45%, rgba(214,120,50,0.5), transparent 70%),
      linear-gradient(180deg, #8d7f70 0%, #a69682 40%, #857565 65%, #b0a08d 100%);
  }
  .photo-right { left: 470px; }
  .photo-right .fill {
    background:
      radial-gradient(ellipse 45% 40% at 30% 55%, rgba(240,160,40,0.6), transparent 70%),
      linear-gradient(180deg, #a39580 0%, #b8a388 38%, #7d7168 68%, #5e5a58 100%);
  }

  .banner { position: absolute; left: 55px; top: 428px; width: 393px; height: 42px; background: var(--orange);
            clip-path: polygon(0 0, 378px 0, 100% 100%, 0 100%); }
  .banner span { position: absolute; left: 39px; top: 7px; color: #fff; font-size: 26px; line-height: 30px; letter-spacing: 0.5px; }
  .pkg-head { left: 93px; font-weight: 700; font-size: 26px; line-height: 30px; color: var(--orange); }
  .pkg-line { left: 93px; font-size: 26px; line-height: 28px; color: var(--ink); }
  .pkg-line.italic { font-style: italic; font-size: 25px; }
  .rule { position: absolute; left: 94px; width: 307px; height: 2px;
          background: linear-gradient(90deg, rgba(27,27,27,0.05), rgba(27,27,27,0.85) 35%, rgba(27,27,27,0.85) 65%, rgba(27,27,27,0.05)); }

  .kennel { position: absolute; left: 597px; top: 515px; width: 260px; text-align: center; }
  .kennel-mark { display: block; width: 62px; height: 62px; margin: 0 auto 14px; border-radius: 50%; background: var(--ink); }
  .kennel-name { font-size: 17px; line-height: 22px; color: var(--ink); white-space: nowrap; letter-spacing: 0.3px; }
  .kennel-rule { display: block; width: 176px; height: 3px; margin: 10px auto 12px; background: var(--ink); }
  .kennel-town { font-size: 17px; line-height: 22px; color: var(--ink); white-space: nowrap; letter-spacing: 0.3px; }

  .service { font-style: italic; font-size: 29px; line-height: 34px; color: var(--ink-soft); }
  .service em { color: var(--orange); font-weight: 700; }
  .enquire { top: 1094px; font-weight: 700; font-size: 22px; line-height: 26px; color: var(--ink-soft); }
  .contact { top: 1129px; display: flex; justify-content: center; }
  .contact span { background: var(--paper); padding: 0 16px; font-size: 21px; line-height: 26px; color: var(--ink-soft); }
  .contact strong { color: var(--orange); font-size: 22px; }
</style>
</head>
<body>
<main class="flyer">
  <div class="frame"></div>

  <header>
    <h1 class="abs center title"><span>TALL HERON PROVISIONS, LLC</span></h1>
    <p class="abs center town">Millbrook, MO</p>
    <p class="abs center tagline">LICENSED SHOOTING PRESERVE</p>
  </header>

  <figure class="photo photo-hero"><div class="fill" role="img" aria-label="Group of hunters standing behind a fallen log lined with harvested pheasants, with a black retriever, in winter woods"></div></figure>

  <div class="banner"><span>HUNTING PACKAGES</span></div>

  <section class="packages">
    <h2 class="abs pkg-head" style="top:479px;">½ DAY UPLAND FIELD HUNTS</h2>
    <p class="abs pkg-line" style="top:512px;">5 Pheasants — $120</p>
    <p class="abs pkg-line" style="top:540px;">7 Chukar — $125</p>
    <div class="rule" style="top:584px;"></div>

    <h2 class="abs pkg-head" style="top:597px;">CONTINENTAL PHEASANT HUNT</h2>
    <p class="abs pkg-line italic" style="top:628px;">12 Pheasants — $325 (includes meal)</p>
    <p class="abs pkg-line italic" style="top:656px;">12 Hunter Minimum</p>
    <div class="rule" style="top:702px;"></div>

    <h2 class="abs pkg-head" style="top:713px;">GUIDES AVAILABLE</h2>
    <p class="abs pkg-line italic" style="top:744px;">$100 per half day</p>
  </section>

  <aside class="kennel">
    <span class="kennel-mark"></span>
    <p class="kennel-name">PINE HOLLOW SETTERS</p>
    <span class="kennel-rule"></span>
    <p class="kennel-town">CEDAR FLATS, MO</p>
  </aside>

  <figure class="photo photo-small photo-left"><div class="fill" role="img" aria-label="Two hunters and a shorthaired pointer behind a log lined with chukar in the woods"></div></figure>
  <figure class="photo photo-small photo-right"><div class="fill" role="img" aria-label="Hunters with a yellow Labrador beside a pickup tailgate holding the day's birds"></div></figure>

  <footer>
    <p class="abs center service" style="top:1011px;">Professional <em>dog training</em> available</p>
    <p class="abs center service" style="top:1047px;">Puppies and started dogs <em>for sale!</em></p>
    <p class="abs center enquire">For More Enquiries, CONTACT:</p>
    <p class="abs center contact"><span><strong>DALE MORGAN</strong> : 660-555-0147</span></p>
  </footer>
</main>
</body>
</html>
```